Business Card Design for Varomir Facility Services

We are looking for a Business Card Design for the Company "Varomir Facility Services."
Front side:
- Company Logo (small)
- Company Name, address, pohone, website and personal data.
- white background, for text e.g. company colors (blue or green like in the logo)
Please use following data:
Company data:
Varomir Facility Services Kostelac
Birkenhaldweg 14
6347 Lindmoos
www.varomir-fs.ch
Person data:
Tarik Kostelac
Geschäftsführer
+41 76 519 47 83
info@varomir-fs.ch
Back side:
could be colored in blue or green
please use a big logo sing and some smaller icons to say what is all beeing offered in facility services, like cleaning, maintenance cleaning
industrial cleaning, caretaking, gardening, disposal. There is no need for everyone of the icons if there are similar or an icon is standing for more of them.
colors to use:
blue: HEX 246BB0
green: HEX 52B33E

```html
<!DOCTYPE html>
<html lang="de">
<head>
<meta charset="utf-8">
<title>Varomir Facility Services – Business Card</title>
<link href="https://fonts.googleapis.com/css2?family=Lato:wght@400;700&display=swap" rel="stylesheet">
<style>
  :root {
    --brand-blue: #246bb0;
    --brand-green: #52b33e;
    --card-black: #111111;
    --stage: #1c1c1c;
    --text-light: #f2f2f2;
    --rule: #3a3a3a;
  }
  * { box-sizing: border-box; margin: 0; padding: 0; }
  html, body { width: 1200px; height: 900px; overflow: hidden; }
  body {
    background: var(--stage);
    font-family: "Lato", Arial, sans-serif;
    position: relative;
  }
  .card {
    position: absolute;
    left: 300px;
    width: 600px;
    height: 340px;
    background: var(--card-black);
    border-radius: 22px;
    box-shadow: 0 16px 40px rgba(0,0,0,.6);
    color: var(--text-light);
  }
  /* back side */
  .card--back { top: 90px; }
  .back-brand {
    position: absolute;
    top: 88px; left: 0; right: 0;
    display: flex; align-items: center; justify-content: center; gap: 16px;
  }
  .brand-dot {
    width: 22px; height: 22px; border-radius: 50%;
    background: var(--brand-green);
  }
  .back-brand .brand-name {
    font-size: 40px; font-weight: 700; letter-spacing: 3px;
    color: var(--brand-blue); text-transform: uppercase;
  }
  .card--back .divider {
    position: absolute; left: 40px; right: 40px; top: 230px;
    height: 1px; background: var(--rule);
  }
  .services {
    position: absolute; left: 40px; right: 40px; top: 246px;
    text-align: center; font-size: 14px; letter-spacing: 1px;
    line-height: 1.45; text-transform: uppercase;
  }
  /* front side */
  .card--front { top: 470px; }
  .front-brand {
    position: absolute; top: 42px; right: 40px;
    display: flex; align-items: center; gap: 12px;
  }
  .front-brand .brand-dot { width: 16px; height: 16px; }
  .front-brand .brand-name {
    font-size: 26px; font-weight: 700; letter-spacing: 2px;
    color: var(--brand-blue); text-transform: uppercase;
  }
  .card--front .divider {
    position: absolute; left: 40px; right: 40px; top: 112px;
    height: 1px; background: var(--rule);
  }
  .company-address {
    position: absolute; top: 130px; right: 40px;
    text-align: right; font-style: normal; font-size: 16px; line-height: 1.3;
  }
  .company-address .company { color: var(--brand-blue); }
  .person {
    position: absolute; left: 40px; top: 186px;
  }
  .person-name {
    color: var(--brand-blue); font-weight: 700; font-size: 21px;
    letter-spacing: 1px; text-transform: uppercase;
  }
  .person-role { color: var(--brand-green); font-size: 16px; margin-bottom: 10px; }
  .contact-list { list-style: none; font-size: 17px; line-height: 1.5; }
  .contact-list li { display: flex; align-items: center; gap: 10px; }
  .contact-icon { width: 15px; height: 15px; fill: var(--brand-blue); flex: none; }
</style>
</head>
<body>

<section class="card card--back" aria-label="Rückseite">
  <div class="back-brand">
    <span class="brand-dot"></span>
    <span class="brand-name">Varomir</span>
  </div>
  <div class="divider"></div>
  <p class="services">
    Cleaning | Maintenance Cleaning | Industrial Cleaning<br>
    Caretaking | Gardening | Disposal
  </p>
</section>

<section class="card card--front" aria-label="Vorderseite">
  <div class="front-brand">
    <span class="brand-dot"></span>
    <span class="brand-name">Varomir Facility Services</span>
  </div>
  <div class="divider"></div>

  <address class="company-address">
    <span class="company">Varomir Facility Services<br>Kostelac</span><br>
    Birkenhaldweg 14<br>
    6347 Lindmoos
  </address>

  <div class="person">
    <p class="person-name">Tarik Kostelac</p>
    <p class="person-role">Geschäftsführer</p>
    <ul class="contact-list">
      <li>
        <svg class="contact-icon" viewBox="0 0 24 24" aria-hidden="true"><path d="M6.6 10.8a15 15 0 0 0 6.6 6.6l2.2-2.2a1 1 0 0 1 1-.25 11.4 11.4 0 0 0 3.6.57 1 1 0 0 1 1 1V20a1 1 0 0 1-1 1A17 17 0 0 1 3 4a1 1 0 0 1 1-1h3.5a1 1 0 0 1 1 1c0 1.25.2 2.45.57 3.6a1 1 0 0 1-.25 1z"/></svg>
        +41 76 519 47 83
      </li>
      <li>
        <svg class="contact-icon" viewBox="0 0 24 24" aria-hidden="true"><path d="M2 5h20v14H2z M2 5l10 8 10-8" stroke="#111" stroke-width="1.5"/></svg>
        info@varomir-fs.ch
      </li>
      <li>
        <svg class="contact-icon" viewBox="0 0 24 24" aria-hidden="true"><circle cx="12" cy="12" r="10"/><path d="M2 12h20M12 2c3 3 3 17 0 20M12 2c-3 3-3 17 0 20" stroke="#111" stroke-width="1.4" fill="none"/></svg>
        www.varomir-fs.ch
      </li>
    </ul>
  </div>
</section>

</body>
</html>
```